Venture Capital Firm Needs Website Redesign

We need a bold revamp of our website (https://halverine.vc/)
which at the moment looks washed out. We want a crisp, fresh and unique look. Feel free to keep as much or as little content in the site. The only thing we need to keep is a team section. The site should convey a clear distinction between our 3 product lines: Venture Capital, Private Credit, and Crypto. Two versions of our logo are attached and they should not change. For design inspirations, we like http://www.9plm.com/ for a more simple site and for a more built out site we like http://bluetorch.com/

Updates
Industry/Entity Type
Investment
Coding
Coded - Design and coding required
Number of Pages Required
1 page
Font styles to use
Colors
Designer to choose colors to be used in the design.
Requirements
Must have
- - Clear distinction between our 3 product lines: Venture Capital, Private Credit
- - Team section

Nice to have
- Some really creative aspect like http://www.9plm.com/ has with the distinction between first, second, and third kind

```html
<!DOCTYPE html>
<html lang="en">
<head>
<meta charset="utf-8">
<title>Halverine — Technology and Novel Asset Classes</title>
<link href="https://fonts.googleapis.com/css2?family=Poppins:wght@400;500;600;700&family=Open+Sans:wght@400;600;700&display=swap" rel="stylesheet">
<style>
:root{
  --green:#6f8d29;
  --green-dark:#5b7620;
  --green-soft:#7f9c35;
  --ink:#222222;
  --text:#3d3d3d;
  --muted:#777777;
  --grey-bg:#efefef;
  --footer-light:#f4f4f4;
  --footer-dark:#2a2d30;
  --white:#ffffff;
}
*{box-sizing:border-box;margin:0;padding:0}
html,body{width:1200px;height:3822px;overflow:hidden;background:var(--white)}
body{font-family:"Open Sans",Arial,sans-serif;color:var(--text);position:relative}
.section{position:absolute;left:0;width:1200px}
h1,h2,h3,.nav,.brand,.btn,.team-name{font-family:"Poppins",Arial,sans-serif}
.btn{position:absolute;display:inline-block;height:34px;line-height:34px;padding:0 26px;border-radius:17px;background:var(--green);color:var(--white);font-size:13px;font-weight:600;text-decoration:none}
.accent{color:var(--green)}

/* hero */
.hero{top:0;height:660px;overflow:hidden}
.hero-photo{position:absolute;inset:0;background:linear-gradient(120deg,#1f2320 0%,#4a4f45 35%,#6b6a5c 55%,#2b2e2a 100%)}
.hero-shade{position:absolute;inset:0;background:rgba(0,0,0,.35)}
.brand{position:absolute;left:133px;top:40px;color:var(--white);font-size:38px;font-weight:500;letter-spacing:1px}
.nav{position:absolute;top:52px;left:472px;display:flex;gap:28px;color:var(--white);font-size:15px;font-weight:600;text-transform:uppercase}
.hero h1{position:absolute;top:228px;left:0;width:1200px;text-align:center;color:var(--white);font-size:44px;line-height:53px;font-weight:700;text-transform:uppercase;text-shadow:0 2px 6px rgba(0,0,0,.4)}
.hero .btn{left:541px;top:404px;border-radius:3px}
.dots{position:absolute;top:544px;left:572px;display:flex;gap:9px}
.dots span{width:10px;height:10px;border-radius:50%;background:var(--white);opacity:.9}
.dots span:first-child{background:transparent;border:2px solid var(--white)}
.hero-curve{position:absolute;left:0;top:580px}

/* welcome */
.welcome{top:660px;height:316px;text-align:center}
.welcome h2{margin-top:10px;font-size:42px;font-weight:600;color:var(--ink)}
.welcome p{width:850px;margin:20px auto 0;font-size:14px;line-height:25px;color:var(--text)}
.welcome .btn{left:544px;top:205px}

/* product lines */
.vc{top:976px;height:502px;background:var(--grey-bg)}
.credit{top:1478px;height:542px;background:var(--white)}
.product h2{position:absolute;font-size:42px;font-weight:600;color:var(--ink)}
.product p{position:absolute;width:430px;font-size:12.5px;line-height:24px;color:var(--text)}
.orbit{position:absolute}
.orbit .photo{position:absolute;border-radius:50%}
.pill{position:absolute;background:var(--white);border-radius:46px;box-shadow:0 3px 10px rgba(0,0,0,.15);display:flex;align-items:center;justify-content:center;font-family:"Poppins",Arial,sans-serif;font-weight:600;font-size:17px;color:var(--ink)}

/* crypto */
.crypto{top:2020px;height:554px;background:linear-gradient(180deg,#6c8a27,#738f2d);text-align:center;color:var(--white)}
.crypto h2{margin-top:60px;font-size:38px;font-weight:700;letter-spacing:1px}
.crypto p{width:760px;margin:14px auto 0;font-size:13.5px;line-height:25px;color:#eef3df}
.crypto .btn{left:544px;top:208px;background:var(--ink)}
.device{top:2311px;left:303px;width:592px;height:263px;background:#1c1c1c;border-radius:22px 22px 0 0}
.chart-card{top:2331px;left:334px;width:530px;height:332px;background:var(--white);box-shadow:0 4px 14px rgba(0,0,0,.18)}

/* team */
.team{top:2700px;height:540px;text-align:center}
.team h2{margin-top:52px;font-size:42px;font-weight:600;color:var(--ink)}
.team .sub{margin-top:4px;font-size:15px;color:var(--ink)}
.card{position:absolute;top:159px;width:217px;height:262px;background:var(--white);border:1px solid #e3e3e3;box-shadow:0 2px 6px rgba(0,0,0,.08)}
.card .photo{height:193px;background:linear-gradient(180deg,#9a9a9a,#5d5d5d)}
.card.active .photo{background:var(--green-soft);color:var(--white);padding:58px 22px 0}
.card .socials{display:flex;justify-content:center;gap:10px;margin-bottom:14px}
.card .socials span{width:30px;height:30px;border-radius:50%;background:var(--white)}
.card .bio{font-size:11.5px;line-height:16px}
.team-name{margin-top:17px;font-size:16px;font-weight:500;color:var(--ink)}
.team-role{font-size:14px;color:var(--text)}
.pager{position:absolute;top:470px;left:558px;display:flex;gap:8px}
.pager span{width:22px;height:3px;background:#9bb35a}
.pager span:first-child{background:var(--ink)}

/* footer */
.footer{top:3295px;height:366px}
.foot-brand{position:absolute;left:0;top:0;width:453px;height:366px;background:var(--green-soft)}
.foot-brand .ring{position:absolute;left:121px;top:96px;width:154px;height:154px;border:4px solid var(--white);border-radius:50%}
.foot-brand .name{position:absolute;left:0;top:260px;width:330px;text-align:center;color:var(--white);font-family:"Poppins",Arial,sans-serif;font-size:34px;font-weight:400;letter-spacing:1px}
.foot-contact{position:absolute;left:453px;top:0;width:350px;height:366px;background:var(--footer-light);padding:80px 0 0 58px}
.foot-contact h3,.foot-form h3{font-size:28px;font-weight:700;color:var(--ink)}
.contact-line{display:flex;gap:10px;margin-top:16px;font-size:13px;line-height:18px;color:var(--text)}
.contact-line svg{flex:none;margin-top:2px}
.foot-contact h4{margin-top:24px;font-family:"Poppins",Arial,sans-serif;font-size:19px;font-weight:600;color:var(--ink)}
.follow{display:flex;gap:7px;margin-top:14px}
.follow span{width:24px;height:24px;border:1px solid #666;border-radius:50%}
.foot-form{position:absolute;left:803px;top:0;width:397px;height:366px;background:linear-gradient(135deg,#2f3336,#23262a);padding:80px 0 0 38px}
.foot-form h3{color:var(--white)}
.field{width:300px;margin-top:22px;padding-bottom:8px;border-bottom:1px solid #6a6d70;font-size:12px;color:#d8d8d8}
.field:first-of-type{margin-top:32px}
.submit{margin-top:22px;display:inline-block;padding:6px 14px;border:1px solid #cfcfcf;color:var(--white);font-size:11px;font-weight:600}
.copyright{top:3770px;text-align:center;font-size:11px;color:var(--text)}
</style>
</head>
<body>

<header class="section hero">
  <div class="hero-photo" role="img" aria-label="Hands holding a tablet at a desk, dark photographic background"></div>
  <div class="hero-shade"></div>
  <div class="brand">HALVERINE</div>
  <nav class="nav"><span>Home</span><span>Venture</span><span>Private Credit</span><span>Crypto</span><span>About</span><span>Team</span><span>Blog</span></nav>
  <h1>Halverine operates at<br>the intersection of technology<br>and novel asset classes.</h1>
  <a class="btn">READ MORE</a>
  <div class="dots"><span></span><span></span><span></span><span></span></div>
  <svg class="hero-curve" width="1200" height="80" viewBox="0 0 1200 80">
    <path d="M0 80 L0 62 Q600 -40 1200 62 L1200 80 Z" fill="#ffffff"/>
    <path d="M40 80 Q600 -22 1200 12" fill="none" stroke="#6f8d29" stroke-width="4"/>
  </svg>
</header>

<section class="section welcome">
  <h2>Welcome to <span class="accent">Halverine</span></h2>
  <p>Halverine operates three businesses that bridge technology and finance. We invest in pre-seed venture capital, and build software for the companies we invest in. We manage direct private credit funds that provide private credit capital to alternative private credit platforms, enabling them to finance the loans they originate. We create crypto funds for individuals, IRAs and institutions to get simple and easy access to cryptocurrencies.</p>
  <a class="btn">Read More</a>
</section>

<section class="section product vc">
  <div class="orbit" style="left:170px;top:58px;width:370px;height:370px">
    <svg width="370" height="370" style="position:absolute;left:0;top:0"><circle cx="182" cy="195" r="170" fill="none" stroke="#1f1f1f" stroke-width="7"/></svg>
    <div class="photo" role="img" aria-label="Two people shaking hands across a meeting table" style="left:26px;top:40px;width:312px;height:312px;background:linear-gradient(150deg,#b9c3c0,#7f8f86 50%,#c9b58b)"></div>
    <div class="pill" style="left:112px;top:0;width:150px;height:62px">Loomwise</div>
    <div class="pill" style="left:-28px;top:130px;width:120px;height:80px;font-size:13px">Marrow Group</div>
    <div class="pill" style="left:244px;top:128px;width:138px;height:80px;font-size:15px">Vistaplay</div>
    <div class="pill" style="left:108px;top:278px;width:140px;height:72px">Playroute</div>
  </div>
  <h2 style="left:630px;top:112px">Venture <span class="accent">Capital</span></h2>
  <p style="left:630px;top:184px">We invest in early-stage startups led by founders who are passionate and knowledgeable about the markets they serve. We have our own software developers and product managers. We work with the founders in our portfolio to help them bring products to market, earning equity for this work and for the cash we invest in their companies.</p>
  <a class="btn" style="left:630px;top:332px">Read More</a>
</section>

<section class="section product credit">
  <h2 style="left:133px;top:140px">Private <span class="accent">Credit</span></h2>
  <p style="left:133px;top:210px;width:470px">Halverine Private Credit provides capital to lending businesses that are focused on using technology to establish new credit markets, create new credit products or dramatically re-invent an existing form of credit. We believe that the pioneers who build something truly different in a credit market will create the most sustainable business models. Given our heritage as a venture firm, we are comfortable with emerging businesses and can provide capital for a company's first loan.</p>
  <a class="btn" style="left:133px;top:378px">Read More</a>
  <div class="orbit" style="left:672px;top:84px;width:370px;height:370px">
    <svg width="370" height="370" style="position:absolute;left:0;top:0"><circle cx="180" cy="195" r="165" fill="none" stroke="#1f1f1f" stroke-width="7"/></svg>
    <div class="photo" role="img" aria-label="Colleagues smiling together around a laptop in an office" style="left:28px;top:44px;width:304px;height:304px;background:linear-gradient(140deg,#d9d4cc,#9aa3a8 45%,#5d6a78)"></div>
    <div class="pill" style="left:116px;top:0;width:132px;height:70px"><svg width="30" height="30"><circle cx="15" cy="15" r="13" fill="#6f8d29"/></svg></div>
    <div class="pill" style="left:-22px;top:148px;width:150px;height:72px;font-size:14px">Fenrow Financial</div>
    <div class="pill" style="left:250px;top:150px;width:130px;height:68px;font-size:16px">Lucidbank</div>
  </div>
</section>

<section class="section crypto">
  <h2>CRYPTO</h2>
  <p>The Halverine Crypto Index tracks the top 5 cryptocurrencies weighted by market cap and rebalanced twice a month. We believe this is the simplest and most cost effective way to obtain cryptocurrency exposure. Our process has been designed by experts from financial services and cryptocurrency industries.</p>
  <a class="btn">Read More</a>
</section>

<div class="section device" style="width:592px"></div>
<div class="section chart-card">
  <svg width="530" height="332" viewBox="0 0 530 332" font-family="Open Sans, Arial, sans-serif">
    <text x="265" y="22" text-anchor="middle" font-size="10" font-weight="600" fill="#333">HCI™ Cumulative Growth</text>
    <circle cx="178" cy="40" r="6" fill="#a7b52a"/><text x="188" y="43" font-size="8" fill="#333">HCI™ (+1,378%)</text>
    <circle cx="268" cy="40" r="6" fill="#111"/><text x="278" y="43" font-size="8" fill="#333">Bitcoin (+711%)</text>
    <g font-size="8" fill="#555" text-anchor="end">
      <text x="62" y="298">0</text><text x="62" y="266">500</text><text x="62" y="234">1000</text><text x="62" y="202">1500</text>
      <text x="62" y="170">2000</text><text x="62" y="138">2500</text><text x="62" y="106">3000</text><text x="62" y="74">3500</text>
    </g>
    <line x1="70" y1="295" x2="490" y2="295" stroke="#999" stroke-width="1"/>
    <g font-size="7" fill="#555" text-anchor="middle">
      <text x="78" y="306">Jan</text><text x="108" y="306">Feb</text><text x="138" y="306">Mar</text><text x="168" y="306">Apr</text><text x="198" y="306">May</text><text x="228" y="306">Jun</text><text x="258" y="306">Jul</text><text x="288" y="306">Aug</text><text x="318" y="306">Sep</text><text x="348" y="306">Oct</text><text x="378" y="306">Nov</text><text x="408" y="306">Dec</text><text x="438" y="306">Jan</text><text x="468" y="306">Feb</text><text x="490" y="306">Mar</text>
    </g>
    <polyline fill="none" stroke="#a7b52a" stroke-width="2.5" points="78,294 108,292 138,290 168,286 198,280 228,275 258,272 288,268 318,262 348,245 368,228 388,200 400,170 410,140 420,110 430,130 440,150 450,165 460,158 470,185 480,205 490,225"/>
    <polyline fill="none" stroke="#111" stroke-width="2" points="78,294 108,293 138,292 168,290 198,287 228,284 258,282 288,279 318,275 348,265 368,252 388,238 400,215 410,200 420,205 430,220 440,240 450,232 460,245 470,255 480,262 490,272"/>
    <text x="265" y="318" text-anchor="middle" font-size="6" fill="#666">Past performance is not a guarantee of future results. Index figures are shown for illustration.</text>
  </svg>
</div>

<section class="section team">
  <h2>Our <span class="accent">Team</span></h2>
  <div class="sub">The very best helping the very best.</div>
  <div class="card active" style="left:133px">
    <div class="photo">
      <div class="socials"><span></span><span></span><span></span></div>
      <div class="bio">Omar Is A Partner For Halverine Vc Fund. He Is Also A Cofounder Of Halverine</div>
    </div>
    <div class="team-name">Omar Haddad</div><div class="team-role">Partner</div>
  </div>
  <div class="card" style="left:372px">
    <div class="photo" role="img" aria-label="Black and white portrait of a team partner"></div>
    <div class="team-name">Rohan Kelkar</div><div class="team-role">Partner</div>
  </div>
  <div class="card" style="left:611px">
    <div class="photo" role="img" aria-label="Black and white portrait of a team partner"></div>
    <div class="team-name">Samir Ghori</div><div class="team-role">Partner</div>
  </div>
  <div class="card" style="left:851px">
    <div class="photo" role="img" aria-label="Black and white portrait of a team partner"></div>
    <div class="team-name">Thomas Bellamy</div><div class="team-role">Partner</div>
  </div>
  <div class="pager"><span></span><span></span><span></span></div>
</section>

<footer class="section footer">
  <div class="foot-brand">
    <div class="ring"></div>
    <div class="name" style="left:32px">HALVERINE</div>
  </div>
  <div class="foot-contact">
    <h3>CONTACT <span class="accent">US</span></h3>
    <div class="contact-line" style="margin-top:22px">
      <svg width="12" height="16" viewBox="0 0 12 16"><path d="M6 0a6 6 0 0 0-6 6c0 4.5 6 10 6 10s6-5.5 6-10a6 6 0 0 0-6-6zm0 8.5A2.5 2.5 0 1 1 6 3.5a2.5 2.5 0 0 1 0 5z" fill="#6f8d29"/></svg>
      <span>215 Mercer Street, Suite 804<br>New York, NY 10012</span>
    </div>
    <div class="contact-line">
      <svg width="14" height="14" viewBox="0 0 14 14"><path d="M3 0l2.5 3.2-1.4 1.8a8 8 0 0 0 4.9 4.9l1.8-1.4L14 11l-2 3C5.5 14 0 8.5 0 2z" fill="#6f8d29"/></svg>
      <span>Phone: +31 (0)6 52718430</span>
    </div>
    <div class="contact-line">
      <svg width="14" height="11" viewBox="0 0 14 11"><rect width="14" height="11" rx="1" fill="#6f8d29"/><path d="M0 1l7 5 7-5" fill="none" stroke="#fff" stroke-width="1.2"/></svg>
      <span>Email: info@halverine.vc</span>
    </div>
    <h4>FOLLOW <span class="accent">US</span></h4>
    <div class="follow"><span></span><span></span><span></span><span></span></div>
  </div>
  <div class="foot-form">
    <h3>GET IN TOUCH</h3>
    <div class="field">Name</div>
    <div class="field">Email</div>
    <div class="field">Message</div>
    <span class="submit">SUBMIT</span>
  </div>
</footer>

<div class="section copyright">Copyright © Halverine 2018. All rights reserved.</div>

</body>
</html>
```